holloway paving service

Needs to have phone number 0418259730 and email markholloway@brightmail.com.au.
ABN 62318470915
name mark holloway

For all your concreting solutions
Excavation
Exposed & colour concrete
House & shed slabs
Driveways
Landing & steps

Contact Information for Business Card

ph 0418259730
email markholloway@brightmail.com.au.
ABN 62318470915
name mark holloway

```html
<!DOCTYPE html>
<html lang="en">
<head>
<meta charset="utf-8">
<title>Holloway Paving Service – Business Cards</title>
<link href="https://fonts.googleapis.com/css2?family=Open+Sans:wght@400;600;700&display=swap" rel="stylesheet">
<style>
  :root {
    --backdrop: #3a3532;
    --card: #141414;
    --card-edge: #1d1d1d;
    --orange: #f26a21;
    --grey: #8a8a8a;
    --light-grey: #b9b9b9;
    --white: #f2f2f2;
  }
  html, body {
    margin: 0;
    padding: 0;
    width: 1200px;
    height: 864px;
    overflow: hidden;
    background: var(--backdrop);
    font-family: "Open Sans", Arial, sans-serif;
  }
  .canvas {
    position: relative;
    width: 1200px;
    height: 864px;
  }
  .card {
    position: absolute;
    width: 540px;
    height: 310px;
    background: var(--card);
    border: 1px solid var(--card-edge);
    box-shadow: 0 14px 30px rgba(0,0,0,0.45);
    box-sizing: border-box;
  }
  /* Back of card: services */
  .card-services {
    left: 40px;
    top: 150px;
  }
  .services-mark {
    position: absolute;
    top: 70px;
    left: 0;
    right: 0;
    display: flex;
    align-items: center;
    justify-content: center;
    gap: 12px;
  }
  .services-mark .mark-square {
    width: 26px;
    height: 26px;
    background: var(--grey);
  }
  .services-mark .mark-name {
    font-weight: 700;
    font-size: 22px;
    letter-spacing: 1px;
    color: var(--grey);
    text-transform: uppercase;
  }
  .services-list {
    position: absolute;
    left: 70px;
    right: 40px;
    bottom: 70px;
    color: var(--light-grey);
    font-size: 15px;
    line-height: 1.5;
  }
  .services-list p { margin: 0; }
  .services-list .line-one { padding-left: 30px; }
  .bullet { margin: 0 6px; }

  /* Front of card: contact */
  .card-contact {
    left: 620px;
    top: 400px;
  }
  .brand-block {
    position: absolute;
    left: 30px;
    top: 105px;
    display: flex;
    align-items: flex-start;
  }
  .brand-square {
    width: 38px;
    height: 38px;
    background: var(--orange);
    margin-top: 6px;
  }
  .brand-divider {
    width: 2px;
    height: 64px;
    background: var(--orange);
    margin: 0 10px 0 10px;
  }
  .brand-text {
    display: flex;
    flex-direction: column;
  }
  .brand-name {
    color: var(--orange);
    font-weight: 700;
    font-size: 15px;
    text-transform: uppercase;
    letter-spacing: 0.2px;
    line-height: 1.2;
    width: 150px;
  }
  .brand-rule {
    height: 1px;
    background: var(--grey);
    width: 170px;
    margin: 5px 0 3px;
  }
  .brand-phone {
    color: var(--orange);
    font-size: 12px;
    font-weight: 600;
    letter-spacing: 1px;
  }
  .contact-block {
    position: absolute;
    left: 280px;
    top: 100px;
    color: var(--white);
  }
  .contact-name {
    color: var(--orange);
    font-weight: 700;
    font-size: 20px;
    text-transform: uppercase;
    margin: 0 0 8px;
  }
  .contact-list {
    list-style: none;
    margin: 0;
    padding: 0;
    font-size: 14px;
    line-height: 1.55;
  }
  .contact-list li {
    display: flex;
    align-items: center;
    gap: 8px;
    white-space: nowrap;
  }
  .contact-list svg { width: 13px; height: 13px; flex: none; }
  .contact-list .abn { padding-left: 0; }
</style>
</head>
<body>
<main class="canvas">

  <section class="card card-services" aria-label="Business card back">
    <div class="services-mark">
      <span class="mark-square"></span>
      <span class="mark-name">Holloway Paving Service</span>
    </div>
    <div class="services-list">
      <p class="line-one">Excavation<span class="bullet">•</span>Exposed &amp; colour concrete</p>
      <p>House &amp; shed slabs<span class="bullet">•</span>Driveways<span class="bullet">•</span>Landing &amp; steps</p>
    </div>
  </section>

  <section class="card card-contact" aria-label="Business card front">
    <div class="brand-block">
      <span class="brand-square"></span>
      <span class="brand-divider"></span>
      <div class="brand-text">
        <span class="brand-name">Holloway Paving Service</span>
        <span class="brand-rule"></span>
        <span class="brand-phone">0418259730</span>
      </div>
    </div>

    <div class="contact-block">
      <h1 class="contact-name">Mark Holloway</h1>
      <ul class="contact-list">
        <li>
          <svg viewBox="0 0 24 24" aria-hidden="true"><path fill="#f26a21" d="M6.6 10.8a15.1 15.1 0 0 0 6.6 6.6l2.2-2.2c.3-.3.7-.4 1-.2 1.1.4 2.3.6 3.6.6.6 0 1 .4 1 1V20c0 .6-.4 1-1 1A17 17 0 0 1 3 4c0-.6.4-1 1-1h3.5c.6 0 1 .4 1 1 0 1.3.2 2.5.6 3.6.1.3 0 .7-.2 1z"/></svg>
          0418259730
        </li>
        <li>
          <svg viewBox="0 0 24 24" aria-hidden="true"><rect x="2" y="5" width="20" height="14" rx="1" fill="#f26a21"/><path d="M2 6l10 7 10-7" stroke="#141414" stroke-width="1.6" fill="none"/></svg>
          markholloway@brightmail.com.au
        </li>
        <li>
          <svg viewBox="0 0 24 24" aria-hidden="true"><circle cx="12" cy="12" r="10" fill="#f26a21"/><path d="M2 12h20M12 2c3 3 3 17 0 20M12 2c-3 3-3 17 0 20" stroke="#141414" stroke-width="1.4" fill="none"/></svg>
          www.hollowaypaving.com.au
        </li>
        <li class="abn">ABN 62318470915</li>
      </ul>
    </div>
  </section>

</main>
</body>
</html>
```